Larkmoor Home Works Sales Flyer

We want a sales flyer that outlines our companies strengths with Kitchen & Bath Remodeling. We would like highlight those aspects while also showcasing our ability to do decks and home additions. We want financing packages to be a big part of the flyer.

Target Market(s)

Residential Customers

Requirements
Must have
• Financing options
Highlight Kitchen & bath remodeling
Less subtle is our decks and home additions
Nice to have
• Keep within our logo colors-we are looking for informative flyers that leave homeowners eager to call us after a meeting

```html
<!DOCTYPE html>
<html lang="en">
<head>
<meta charset="utf-8">
<title>Larkmoor Home Works – Sales Flyer</title>
<link href="https://fonts.googleapis.com/css2?family=Source+Sans+3:wght@300;400;600;700&display=swap" rel="stylesheet">
<style>
  :root {
    --sky: #12b4f2;
    --azure: #1a8ee0;
    --royal: #1246b8;
    --navy: #1234a0;
    --heading-blue: #1f7fd6;
    --ink: #3a3d44;
    --paper: #ffffff;
    --mist: #eceef1;
    --backdrop: #dcdcdc;
  }
  * { box-sizing: border-box; margin: 0; padding: 0; }
  html, body { width: 1200px; height: 1200px; overflow: hidden; }
  body {
    background: var(--backdrop);
    font-family: "Source Sans 3", "Myriad Pro", sans-serif;
    color: var(--ink);
    position: relative;
  }
  .flyer {
    position: absolute; left: 170px; top: 44px;
    width: 860px; height: 1111px;
    background: var(--paper);
    overflow: hidden;
  }
  /* header */
  .masthead {
    position: absolute; left: 0; top: 0; width: 860px; height: 158px;
    background: linear-gradient(120deg, var(--sky) 0%, #1aa5ee 50%, var(--azure) 100%);
    color: var(--paper);
  }
  .brand {
    position: absolute; left: 84px; top: 52px; width: 300px;
    text-align: center;
  }
  .brand-name {
    font-size: 34px; font-weight: 600; letter-spacing: 1px; line-height: 1.05;
    text-transform: uppercase;
  }
  .call-out {
    position: absolute; left: 590px; top: 36px; width: 270px;
    text-align: center; font-weight: 300; font-size: 19px; line-height: 26px;
    text-transform: uppercase;
  }
  .call-out strong { font-weight: 700; }
  .call-out .phone {
    display: flex; align-items: center; justify-content: center; gap: 6px;
    font-size: 25px; font-weight: 600; margin-top: 2px; letter-spacing: .5px;
  }
  /* hero */
  .hero { position: absolute; left: 0; top: 158px; width: 860px; height: 348px; }
  .hero-photo { position: absolute; inset: 0; }
  .hero-photo.kitchen {
    background: linear-gradient(160deg, #c9c4bb 0%, #8f8a83 40%, #6d7380 70%, #4f5560 100%);
    clip-path: polygon(0 0, 492px 0, 415px 100%, 0 100%);
  }
  .hero-photo.bath {
    background: linear-gradient(200deg, #e9eaec 0%, #b9bdc3 40%, #8e949c 75%, #6f747b 100%);
    clip-path: polygon(496px 0, 100% 0, 100% 100%, 419px 100%);
  }
  .hero-divider { position: absolute; inset: 0; }
  .hero-panel {
    position: absolute; left: 0; top: 119px; width: 447px; height: 141px;
    background: rgba(40, 120, 230, 0.62);
    padding: 18px 0 0 54px; color: var(--paper);
    font-size: 31px; font-weight: 400; line-height: 33px;
  }
  .hero-panel b { font-weight: 700; }
  .hero-slogan {
    position: absolute; left: 56px; top: 272px; width: 780px;
    color: var(--paper); font-weight: 600; font-size: 32px; line-height: 31px;
    text-transform: uppercase; letter-spacing: -.3px;
    text-shadow: 0 1px 4px rgba(0,0,0,.45);
  }
  .finance-band {
    position: absolute; left: 0; top: 506px; width: 860px; height: 28px;
    background: linear-gradient(90deg, #0da6ec, var(--azure) 60%, #1a72d6);
    color: var(--paper); text-align: center;
    font-size: 18px; font-weight: 600; line-height: 28px; letter-spacing: .2px;
  }
  /* services */
  .service {
    position: absolute; width: 430px; overflow: hidden;
    background: linear-gradient(180deg, var(--paper) 0%, var(--mist) 100%);
  }
  .service.kitchen { left: 0; top: 534px; height: 244px; }
  .service.bath { left: 430px; top: 534px; height: 244px; background: linear-gradient(180deg, #f7f8f9 0%, var(--mist) 100%); }
  .service.additions { left: 0; top: 778px; height: 279px; background: linear-gradient(180deg, var(--paper) 0%, #f0f1f3 100%); }
  .service.decks { left: 430px; top: 778px; height: 279px; background: linear-gradient(180deg, var(--paper) 0%, #f4f5f6 100%); }
  .service-icon { position: absolute; left: 24px; top: 18px; width: 46px; height: 46px; }
  .service h2 {
    position: absolute; left: 87px; top: 18px;
    font-size: 17px; font-weight: 600; color: var(--heading-blue); text-transform: uppercase;
  }
  .service .intro {
    position: absolute; left: 88px; top: 44px; width: 330px;
    font-size: 13.5px; line-height: 14px; font-weight: 400;
  }
  .service ul {
    position: absolute; left: 88px; list-style: none;
    font-size: 13.5px; line-height: 15.5px;
  }
  .service li { position: relative; padding-left: 12px; }
  .service li::before {
    content: ""; position: absolute; left: 0; top: 6px; width: 4px; height: 4px; background: var(--royal);
  }
  .service.kitchen ul { top: 89px; }
  .service.bath ul { top: 103px; line-height: 14px; }
  .service.bath li { margin-bottom: 3px; }
  .service.additions ul { top: 92px; line-height: 17px; }
  .service.decks ul { top: 120px; line-height: 17px; }
  .service.additions h2 { left: 90px; }
  .service.additions .intro { left: 91px; }
  .service.additions ul { left: 91px; }
  .service.decks h2, .service.decks .intro, .service.decks ul { left: 93px; }
  .service-photo { position: absolute; }
  .service.bath .service-photo {
    left: 275px; top: 96px; width: 155px; height: 148px;
    background: linear-gradient(160deg, #e6e8ea 0%, #b4b9c0 50%, #d8d4cc 100%);
  }
  .service.additions .service-photo {
    left: 244px; top: 109px; width: 186px; height: 170px;
    background: linear-gradient(170deg, #d9d5cc 0%, #efeeea 45%, #a39580 100%);
  }
  .service.decks .service-photo {
    left: 246px; top: 109px; width: 184px; height: 170px;
    background: linear-gradient(180deg, #b78554 0%, #8fb16c 40%, #6f8f55 65%, #6a4a34 100%);
  }
  /* footer */
  .footer {
    position: absolute; left: 0; top: 1057px; width: 860px; height: 54px;
    background: linear-gradient(90deg, var(--navy), var(--royal) 70%, #1a5fce);
    border-top: 3px solid #1e8ff0;
    color: var(--paper); font-size: 15px;
    display: flex; align-items: center; padding-left: 25px; gap: 50px;
  }
  .footer span { display: flex; align-items: center; gap: 12px; }
</style>
</head>
<body>
<main class="flyer">
  <header class="masthead">
    <div class="brand"><div class="brand-name">Larkmoor Home Works</div></div>
    <div class="call-out">
      Call today for your<br><strong>Free</strong> estimate
      <div class="phone">
        <svg width="12" height="12" viewBox="0 0 12 12" aria-hidden="true"><circle cx="6" cy="6" r="6" fill="#e0483e"/><path d="M3.6 3.4c.3-.3.7-.3.9 0l.6.8-.5.6c.3.6.8 1.1 1.4 1.4l.6-.5.8.6c.3.2.3.6 0 .9l-.4.4C5.6 7.4 4.3 6.1 3.3 4.2z" fill="#fff"/></svg>
        555-014-2277
      </div>
    </div>
  </header>

  <section class="hero">
    <div class="hero-photo kitchen" role="img" aria-label="Bright open-plan kitchen with granite island, stone fireplace wall and living area"></div>
    <div class="hero-photo bath" role="img" aria-label="Remodeled bathroom with glass walk-in marble shower and white vanity"></div>
    <svg class="hero-divider" width="860" height="348" aria-hidden="true"><line x1="494" y1="0" x2="417" y2="348" stroke="#fff" stroke-width="3"/></svg>
    <div class="hero-panel">Ready for<br>a Beautiful and Functional<br><b>Kitchen</b> or <b>Bathroom</b>?</div>
    <h1 class="hero-slogan">Work with a top-rated local remodeling company in Brookvale, IA</h1>
  </section>

  <div class="finance-band">$ FINANCING OPTIONS AVAILABLE $</div>

  <section class="service kitchen">
    <svg class="service-icon" viewBox="0 0 46 46" fill="none" stroke="#1f6fd0" stroke-width="1.8" aria-hidden="true">
      <rect x="1" y="20" width="44" height="24"/><line x1="23" y1="20" x2="23" y2="44"/>
      <rect x="5" y="26" width="14" height="6"/><rect x="27" y="26" width="14" height="6"/>
      <line x1="5" y1="37" x2="19" y2="37"/><circle cx="12" cy="12" r="4"/><path d="M6 4v8M4 6h6M32 8h10l-2-4h-6z"/>
    </svg>
    <h2>Kitchen Remodeling</h2>
    <p class="intro">Whatever your vision is for your new kitchen, our crew can help you bring it to life. You can trust us for:</p>
    <ul>
      <li>Open concept design services</li>
      <li>Kitchen cabinet installation services</li>
      <li>Kitchen countertop installation services</li>
      <li>Tile installation services</li>
      <li>Lighting installation services</li>
      <li>Plumbing upgrade services</li>
      <li>Electrical upgrade services</li>
      <li>Drywall services</li>
      <li>Painting services</li>
    </ul>
  </section>

  <section class="service bath">
    <svg class="service-icon" viewBox="0 0 46 46" fill="none" stroke="#1f6fd0" stroke-width="1.8" aria-hidden="true">
      <circle cx="25" cy="8" r="7"/><line x1="21" y1="11" x2="29" y2="5"/>
      <rect x="2" y="24" width="42" height="20"/><rect x="8" y="30" width="30" height="8"/>
      <path d="M14 24c0-4 4-6 9-6s9 2 9 6M6 24v-6h4v6"/>
    </svg>
    <h2>Bathroom Remodeling</h2>
    <p class="intro">When you hire us for your bathroom remodeling project, the possibilities are endless. Our experienced and talented team can:</p>
    <ul>
      <li>Install a custom tile shower</li>
      <li>Build a new vanity</li>
      <li>Install flooring and tile</li>
      <li>Replace your plumbing and<br>light fixtures</li>
      <li>Jetted tubs</li>
      <li>Steam showers</li>
    </ul>
    <div class="service-photo" role="img" aria-label="Marble bathroom with glass shower and double vanity"></div>
  </section>

  <section class="service additions">
    <svg class="service-icon" viewBox="0 0 46 46" fill="none" stroke="#1f6fd0" stroke-width="1.8" aria-hidden="true">
      <path d="M2 44h40V26M2 44V32h10V20h10V8h20v18"/><path d="M16 2v8M26 2v8M36 2v8M14 14l20-12"/>
    </svg>
    <h2>Home Additions</h2>
    <p class="intro">No matter what kind of space you need, our team will bring your vision to life. You can hire us if you need a:</p>
    <ul>
      <li>Bathroom addition</li>
      <li>Bedroom addition</li>
      <li>Garage addition</li>
      <li>Basement addition</li>
      <li>Guest room addition</li>
      <li>Living room addition</li>
      <li>Sunroom addition</li>
    </ul>
    <div class="service-photo" role="img" aria-label="Bright new bedroom addition with made bed and wood floor"></div>
  </section>

  <section class="service decks">
    <svg class="service-icon" viewBox="0 0 46 46" fill="none" stroke="#1f6fd0" stroke-width="1.8" aria-hidden="true">
      <path d="M6 16a17 14 0 0 1 34 0z"/><line x1="23" y1="16" x2="23" y2="40"/>
      <path d="M2 36h42M6 36v6M40 36v6M30 36l8-10"/>
    </svg>
    <h2>Decks/Patios</h2>
    <p class="intro">An outdoor space is a great addition to any residential property. When you decide to build a patio or deck, you'll be able to experience a variety of benefits. Your outdoor area will increase your:</p>
    <ul>
      <li>Property value</li>
      <li>Curb appeal</li>
      <li>Functional living<br>space</li>
    </ul>
    <div class="service-photo" role="img" aria-label="Screened porch with wooden dining set overlooking green trees"></div>
  </section>

  <footer class="footer">
    <span>
      <svg width="13" height="13" viewBox="0 0 14 14" fill="none" stroke="#fff" stroke-width="1" aria-hidden="true"><circle cx="7" cy="7" r="6"/><ellipse cx="7" cy="7" rx="2.6" ry="6"/><path d="M1 7h12M2 4h10M2 10h10"/></svg>
      www.larkmoorhomeworks.com
    </span>
    <span>
      <svg width="14" height="10" viewBox="0 0 14 10" fill="none" stroke="#fff" stroke-width="1" aria-hidden="true"><rect x=".5" y=".5" width="13" height="9"/><path d="M.5 .5L7 6l6.5-5.5"/></svg>
      hello@larkmoorhomeworks.com
    </span>
  </footer>
</main>
</body>
</html>
```